Keystone Trench Co Business Card*

Looking for a professional, clean and crisp business card

I am in the underground utilities industry and am just looking for a really impressive business card. I would like our card to be white with our symbol crisp and clear with it protruding. I also have a business partner that will require his name and info on the card once the design is set. I would like to have our website info on the card which is;
http://keystonetrenchco.example/

Contact Information for Business Card

Website, contact name, number and email

```html
<!DOCTYPE html>
<html lang="en">
<head>
<meta charset="utf-8">
<title>Keystone Trench Co – Business Card</title>
<link rel="stylesheet" href="https://fonts.googleapis.com/css2?family=Oswald:wght@400;500;700&display=swap">
<style>
  :root {
    --backdrop: #dfe2e4;
    --card: #f7f7f5;
    --ink: #1c1c1c;
    --brand-blue: #2f62b8;
    --brand-red: #e1262c;
    --text-grey: #4a4a4a;
    --edge-blue: #1f3f8f;
  }
  * { box-sizing: border-box; margin: 0; padding: 0; }
  html, body {
    width: 1200px; height: 824px; overflow: hidden;
    background: var(--backdrop);
  }
  .canvas {
    width: 1200px; height: 824px;
    display: flex; align-items: center; justify-content: center;
  }
  .card {
    position: relative;
    width: 400px; height: 710px;
    background: var(--card);
    border-bottom: 3px solid var(--edge-blue);
    box-shadow: 0 6px 18px rgba(0,0,0,0.18);
    font-family: "Oswald", sans-serif;
  }
  .contact {
    position: absolute;
    left: 62px; top: 58px;
    width: 300px;
  }
  .contact__name {
    font-weight: 700;
    font-size: 38px;
    line-height: 1;
    color: var(--brand-blue);
    letter-spacing: 0.5px;
    text-transform: uppercase;
  }
  .contact__role {
    display: flex; align-items: center; gap: 10px;
    margin-top: 4px;
    width: 284px;
  }
  .contact__rule {
    flex: 1; height: 2px; background: var(--brand-blue);
  }
  .contact__title {
    font-weight: 700; font-size: 19px;
    color: var(--brand-red);
    text-transform: uppercase;
    letter-spacing: 0.5px;
  }
  .contact__phone {
    margin-top: 6px;
    font-weight: 400; font-size: 37px; line-height: 1.05;
    color: var(--text-grey);
    letter-spacing: 1px;
  }
  .contact__line {
    font-weight: 400; font-size: 15px; line-height: 1.35;
    color: var(--text-grey);
    text-transform: uppercase;
    letter-spacing: 1.6px;
  }
  .brand {
    position: absolute;
    left: 0; right: 0; top: 300px; bottom: 40px;
    display: flex; flex-direction: column; align-items: center; justify-content: center;
    gap: 22px;
  }
  .brand__dot {
    width: 56px; height: 56px; border-radius: 50%;
    background: var(--ink);
  }
  .brand__name {
    font-weight: 700; font-size: 40px; line-height: 1.05;
    color: var(--ink);
    text-transform: uppercase;
    text-align: center;
    letter-spacing: 1px;
  }
</style>
</head>
<body>
  <main class="canvas">
    <article class="card">
      <section class="contact">
        <h1 class="contact__name">Daniel Rourke</h1>
        <div class="contact__role">
          <span class="contact__rule"></span>
          <span class="contact__title">President</span>
          <span class="contact__rule"></span>
        </div>
        <p class="contact__phone">555-014-2273</p>
        <p class="contact__line">info@keystonetrenchco.example</p>
        <p class="contact__line">www.keystonetrenchco.example</p>
      </section>
      <section class="brand">
        <span class="brand__dot"></span>
        <p class="brand__name">Keystone<br>Trench Co</p>
      </section>
    </article>
  </main>
</body>
</html>
```